LHP Regal Business Card Design 2020

Your Manor Steward is looking for a business card that is clean and straight to the point but still looks high-end and attractive. We are a team comprised of management and field professionals focused on the high-end residential marketplace. We serve homeowners and trade professionals directly based out of the Metrowest/Boston area. We provide client services as well as construction/renovation services.
We are aiming for a black and white feel (white background and black text) and a matte finish with rounded edges.

We want to emphasis our vision of "Properties - Projects - Partners".
Dana Pellham is the president of LHP

Please include the following areas we service: Boston/Cape/Newport
Please make sure to include Dana's mobile (555) 213 4480 & office number (555) 640 1937, email dana@yourmanorsteward.example and website www.yourmanorsteward.example

Colors

Designer to choose only greyscale colors for use in the design.

Requirements
Must have
• Include "Properties - Projects - Partners" in design

Include "After Hours Emergency Support # 1800 555 0142" with icon

```html
<!DOCTYPE html>
<html lang="en">
<head>
<meta charset="utf-8">
<title>LHP Business Card</title>
<link rel="stylesheet" href="https://fonts.googleapis.com/css2?family=Montserrat:wght@300;400;600;700&family=Oswald:wght@500&display=swap">
<style>
  :root {
    --backdrop: #1c1c1c;
    --card: #ffffff;
    --ink: #222222;
    --ink-soft: #4a4a4a;
    --rule: #8a8a8a;
  }
  * { box-sizing: border-box; margin: 0; padding: 0; }
  html, body { width: 1200px; height: 930px; overflow: hidden; }
  body {
    background: var(--backdrop);
    font-family: "Montserrat", sans-serif;
    color: var(--ink);
    position: relative;
  }
  .card {
    position: absolute;
    width: 540px;
    height: 310px;
    background: var(--card);
    border-radius: 22px;
  }
  .card--front { left: 90px; top: 130px; }
  .card--back { left: 570px; top: 490px; }

  /* Front */
  .brand {
    position: absolute;
    left: 0; right: 0; top: 44px;
    text-align: center;
  }
  .brand__mark {
    font-weight: 700;
    font-size: 92px;
    line-height: 1;
    letter-spacing: -2px;
    color: var(--ink);
  }
  .brand__name {
    margin-top: 6px;
    font-weight: 700;
    font-size: 17px;
    letter-spacing: 2px;
    text-transform: uppercase;
  }
  .service {
    position: absolute;
    left: 0; right: 0; top: 198px;
    text-align: center;
  }
  .service__title {
    font-weight: 700;
    font-size: 16px;
    letter-spacing: 1px;
  }
  .service__areas {
    margin-top: 14px;
    font-weight: 300;
    font-size: 14px;
    letter-spacing: 1px;
    color: var(--ink-soft);
  }

  /* Back */
  .person {
    position: absolute;
    left: 20px; top: 92px;
    width: 218px;
    text-align: right;
  }
  .person__name {
    font-family: "Oswald", sans-serif;
    font-weight: 500;
    font-size: 30px;
    letter-spacing: 1px;
    text-transform: uppercase;
    line-height: 1.1;
  }
  .person__role {
    font-weight: 400;
    font-size: 13px;
    color: var(--ink-soft);
    letter-spacing: 0.5px;
  }
  .divider {
    position: absolute;
    left: 256px; top: 70px;
    width: 1px; height: 94px;
    background: var(--rule);
  }
  .contact {
    position: absolute;
    left: 274px; top: 74px;
    list-style: none;
  }
  .contact__item {
    display: flex;
    align-items: center;
    gap: 7px;
    font-size: 12px;
    line-height: 22px;
    color: var(--ink);
  }
  .contact__item svg { width: 11px; height: 11px; flex: none; }
  .vision {
    position: absolute;
    left: 0; right: 0; bottom: 76px;
    text-align: center;
    font-weight: 600;
    font-size: 18px;
    letter-spacing: 1px;
    text-transform: uppercase;
  }
  .emergency {
    position: absolute;
    left: 0; right: 0; bottom: 40px;
    display: flex;
    justify-content: center;
    align-items: center;
    gap: 8px;
    font-size: 12px;
    font-weight: 400;
    color: var(--ink-soft);
    letter-spacing: 0.3px;
  }
  .emergency svg { width: 13px; height: 13px; flex: none; color: var(--ink); }
  .emergency strong { font-weight: 600; color: var(--ink); }
</style>
</head>
<body>
  <section class="card card--front">
    <div class="brand">
      <div class="brand__mark">LHP</div>
      <div class="brand__name">Your Manor Steward</div>
    </div>
    <div class="service">
      <div class="service__title">WE SERVICE</div>
      <div class="service__areas">BOSTON | METROWEST | SOUTH SHORE | CAPE/NEWPORT</div>
    </div>
  </section>

  <section class="card card--back">
    <div class="person">
      <div class="person__name">Dana Pellham</div>
      <div class="person__role">President</div>
    </div>
    <div class="divider"></div>
    <ul class="contact">
      <li class="contact__item">
        <svg viewBox="0 0 12 12"><rect x="3" y="0.8" width="6" height="10.4" rx="1.2" fill="none" stroke="currentColor" stroke-width="1.2"/><circle cx="6" cy="9.3" r="0.7" fill="currentColor"/></svg>
        (555) 213 4480
      </li>
      <li class="contact__item">
        <svg viewBox="0 0 12 12"><path d="M2.5 1 L4.5 1 L5.3 3.4 L4 4.4 Q5 6.8 7.6 8 L8.6 6.7 L11 7.5 L11 9.5 Q10.5 11 9 11 Q1 10 1 2.5 Q1 1 2.5 1 Z" fill="currentColor"/></svg>
        (555) 640 1937
      </li>
      <li class="contact__item">
        <svg viewBox="0 0 12 12"><rect x="0.8" y="2.3" width="10.4" height="7.4" fill="none" stroke="currentColor" stroke-width="1.1"/><path d="M0.8 2.6 L6 6.6 L11.2 2.6" fill="none" stroke="currentColor" stroke-width="1.1"/></svg>
        dana@yourmanorsteward.example
      </li>
      <li class="contact__item">
        <svg viewBox="0 0 12 12" fill="none" stroke="currentColor" stroke-width="1"><circle cx="6" cy="6" r="5"/><ellipse cx="6" cy="6" rx="2.2" ry="5"/><path d="M1 6 H11 M2 3.3 H10 M2 8.7 H10"/></svg>
        www.yourmanorsteward.example
      </li>
    </ul>
    <div class="vision">Properties - Projects - Partners</div>
    <div class="emergency">
      <svg viewBox="0 0 14 14"><path d="M3 1 L5.2 1 L6 3.6 L4.6 4.7 Q5.7 7.3 8.4 8.6 L9.5 7.2 L12.2 8 L12.2 10.3 Q11.6 12 10 12 Q1.5 11 1.5 2.6 Q1.5 1 3 1 Z" fill="currentColor"/><path d="M9 1.5 L9 4.2 M9 5.4 L9 5.9" stroke="currentColor" stroke-width="1.3" stroke-linecap="round"/></svg>
      After Hours Emergency Support # <strong>1800 555 0142</strong>
    </div>
  </section>
</body>
</html>
```